New website for a business that provides Tidewell Clinic

A new website that details the services that are provided around Tidewell Clinic for people with a disability through QPKV. There also needs to incorporate an about us and a staff page, Plus a referral form that is a google doc.
The business already has a web address that needs to be tailored.
Soft colours are preferred.
Do not have lots of pictures, keep them minimal.
A logo for the business is also needed to be incorporated, and this is a separate project that can be awarded to the website winner.
Website needs to be able to be used on WIX who will be the host for the design.

Target Market(s)

QPKV clients requiring behaviour support clician

Industry/Entity Type

Clinical behaviour support and analysis

Colors
00AB8E
00BBA5
67D7C9
C6EFE9
E9F9F6

Requirements
Must have
• Soft colours, preferable pale turquoise, minimal pictures, clean, sophisticated and classical look

```html
<!DOCTYPE html>
<html lang="en">
<head>
<meta charset="UTF-8">
<title>Tidewell Clinic</title>
<link rel="stylesheet" href="https://fonts.googleapis.com/css2?family=Libre+Baskerville:wght@400;700&display=swap">
<style>
:root{
  --teal:#00AB8E;
  --teal-bright:#00BBA5;
  --teal-soft:#67D7C9;
  --teal-pale:#C6EFE9;
  --teal-mist:#E9F9F6;
  --ink:#111111;
  --body:#3a3a3a;
  --white:#ffffff;
  --black:#000000;
  --accent:#e2581c;
}
*{margin:0;padding:0;box-sizing:border-box}
html,body{width:1200px;height:3129px;overflow:hidden}
body{position:relative;background:var(--white);font-family:"Libre Baskerville",Georgia,serif;color:var(--ink)}
.abs{position:absolute}
.btn{position:absolute;display:flex;align-items:center;justify-content:center;background:var(--teal);color:var(--white);border-radius:22px;font-weight:700;font-size:16px;text-decoration:none;white-space:nowrap}

/* hero */
.hero{left:0;top:0;width:1200px;height:684px;background:linear-gradient(90deg,#f3f5f6 0%,#e8ecef 35%,#9aa6b0 60%,#3f4f66 80%,#1c2a44 100%)}
.brand{left:112px;top:80px;font-size:30px;font-weight:400;white-space:nowrap;color:var(--ink)}
.nav{left:468px;top:43px;display:flex;gap:26px;font-size:16px;white-space:nowrap}
.nav a{color:var(--ink);text-decoration:none}
.nav a.active{border-bottom:1px solid var(--accent);padding-bottom:4px}
.hero-welcome{left:117px;top:252px;font-size:43px;color:var(--teal)}
.hero-title{left:112px;top:322px;font-size:84px;font-weight:700;line-height:86px}

/* sections */
.section-title{left:0;width:1200px;text-align:center;font-size:50px;font-weight:700}
.arrow{position:absolute;width:36px;height:36px}
.card-photo{position:absolute;width:307px;height:243px}
.card-label{position:absolute;width:249px;height:81px;background:var(--white);box-shadow:0 4px 10px rgba(0,0,0,.12)}
.card-icon{position:absolute;width:68px;height:63px;background:var(--teal);border-radius:3px;display:flex;align-items:center;justify-content:center}
.card-name{position:absolute;font-size:18px;font-weight:700;white-space:nowrap}
.card-role{position:absolute;font-size:13px;color:var(--accent)}

.about-text{left:200px;top:1314px;width:800px;text-align:center;font-size:17px;line-height:28.5px;color:var(--body)}

/* newsletter */
.newsletter{left:0;top:2484px;width:1200px;height:258px;background:var(--teal-pale)}
.newsletter-photo{left:0;top:2484px;width:560px;height:258px;background:linear-gradient(90deg,#8a9488 0%,#b8c6c0 35%,#c8e6df 65%,rgba(198,239,233,0) 100%)}
.news-title{left:407px;top:2542px;font-size:46px;font-weight:700;white-space:nowrap}
.email{left:407px;top:2631px;width:474px;height:46px;background:var(--white);border-radius:23px;font-size:11px;color:#777;padding:16px 22px}

/* footer */
.footer{left:0;top:2742px;width:1200px;height:387px;background:var(--black);color:var(--white)}
.footer-brand{left:0;width:1200px;top:2860px;text-align:center;font-size:40px;font-weight:400;color:var(--white)}
.footer-nav a{position:absolute;top:2976px;font-size:17px;color:var(--white);text-decoration:none;transform:translateX(-50%);white-space:nowrap}
.social{position:absolute;top:3031px;width:24px;height:24px;border:2px solid var(--white);border-radius:4px}
.copyright{left:0;width:1200px;top:3098px;text-align:center;font-size:13px;color:var(--white)}
</style>
</head>
<body>

<!-- Hero -->
<div class="abs hero" role="img" aria-label="Photo of a person's hand on the wheel of a wheelchair"></div>
<div class="abs brand">Tidewell Clinic</div>
<nav class="abs nav">
  <a class="active" href="#">Home</a><a href="#">About Us</a><a href="#">Staffs</a><a href="#">Blog</a><a href="#">Contact Us</a>
</nav>
<a class="btn" href="#" style="left:915px;top:35px;width:170px;height:39px">Explore More</a>
<div class="abs hero-welcome">Welcome to</div>
<h1 class="abs hero-title">Tidewell<br>Clinic</h1>
<a class="btn" href="#" style="left:115px;top:528px;width:171px;height:38px">Contact Us</a>

<!-- Services -->
<h2 class="abs section-title" style="top:762px">Our Services</h2>
<svg class="arrow" style="left:49px;top:957px" viewBox="0 0 36 36"><circle cx="18" cy="18" r="18" fill="var(--teal-bright)"/><path d="M26 18H11M17 11l-7 7 7 7" stroke="#fff" stroke-width="4" fill="none" stroke-linecap="round" stroke-linejoin="round"/></svg>
<svg class="arrow" style="left:1113px;top:957px" viewBox="0 0 36 36"><circle cx="18" cy="18" r="18" fill="var(--teal-bright)"/><path d="M10 18h15M19 11l7 7-7 7" stroke="#fff" stroke-width="4" fill="none" stroke-linecap="round" stroke-linejoin="round"/></svg>

<div class="card-photo" style="left:112px;top:860px;background:linear-gradient(135deg,#6f8a5a,#c7b98f 50%,#3d4a44)" role="img" aria-label="Photo of a carer with an elderly woman in a wheelchair"></div>
<div class="card-label" style="left:152px;top:1075px"></div>
<div class="card-icon" style="left:135px;top:1083px"><svg width="40" height="40" viewBox="0 0 40 40" fill="none" stroke="#fff" stroke-width="2"><path d="M6 20 20 8l14 12v14H6z"/><circle cx="20" cy="23" r="5"/></svg></div>
<div class="card-name" style="left:221px;top:1103px">Home Aged Care</div>

<div class="card-photo" style="left:446px;top:860px;background:linear-gradient(135deg,#8a7a4a,#c98e5a 45%,#2e3a4e)" role="img" aria-label="Photo of two young people, one in a wheelchair, reading together outdoors"></div>
<div class="card-label" style="left:486px;top:1075px"></div>
<div class="card-icon" style="left:469px;top:1083px"><svg width="40" height="40" viewBox="0 0 40 40" fill="none" stroke="#fff" stroke-width="2"><path d="M6 20 20 8l14 12v14H6z"/><circle cx="20" cy="23" r="5"/></svg></div>
<div class="card-name" style="left:555px;top:1103px">Personal Care</div>

<div class="card-photo" style="left:779px;top:860px;background:linear-gradient(135deg,#c8a0a8,#8e9aa8 50%,#4a5a6e)" role="img" aria-label="Photo of young people playing basketball with a wheelchair user"></div>
<div class="card-label" style="left:819px;top:1075px"></div>
<div class="card-icon" style="left:802px;top:1083px"><svg width="40" height="40" viewBox="0 0 40 40" fill="none" stroke="#fff" stroke-width="2"><path d="M6 20 20 8l14 12v14H6z"/><circle cx="20" cy="23" r="5"/></svg></div>
<div class="card-name" style="left:888px;top:1103px">Physical Activites</div>

<!-- About -->
<h2 class="abs section-title" style="top:1235px">About Us</h2>
<p class="abs about-text">Lorem ipsum dolor sit amet, consectetur adipiscing elit, sed do eiusmod tempor incididunt ut labore et dolore magna aliqua. Ut enim ad minim veniam, quis nostrud exercitation ullamco laboris nisi ut aliquip ex ea commodo consequat. Duis aute irure dolor in reprehenderit in voluptate velit esse cillum dolore eu fugiat nulla pariatur. Excepteur sint occaecat cupidatat non proident, sunt in culpa qui officia deserunt mollit anim id est laborum.</p>
<a class="btn" href="#" style="left:514px;top:1487px;width:171px;height:38px">Read More</a>
<div class="abs" style="left:0;top:1530px;width:1200px;height:401px;background:linear-gradient(180deg,#f4f5f5 0%,#e6e2dc 45%,#c9b48a 75%,#8a7a5c 100%)" role="img" aria-label="Photo of a teacher helping a student at a microscope in a classroom"></div>

<!-- Staffs -->
<h2 class="abs section-title" style="top:2009px">Our Staffs</h2>
<svg class="arrow" style="left:49px;top:2196px" viewBox="0 0 36 36"><circle cx="18" cy="18" r="18" fill="var(--teal-bright)"/><path d="M26 18H11M17 11l-7 7 7 7" stroke="#fff" stroke-width="4" fill="none" stroke-linecap="round" stroke-linejoin="round"/></svg>
<svg class="arrow" style="left:1113px;top:2196px" viewBox="0 0 36 36"><circle cx="18" cy="18" r="18" fill="var(--teal-bright)"/><path d="M10 18h15M19 11l7 7-7 7" stroke="#fff" stroke-width="4" fill="none" stroke-linecap="round" stroke-linejoin="round"/></svg>

<div class="card-photo" style="left:112px;top:2100px;background:linear-gradient(160deg,#b9a890,#8a6a52 50%,#1f4e45)" role="img" aria-label="Portrait photo of a smiling staff member"></div>
<div class="card-label" style="left:152px;top:2314px"></div>
<div class="card-icon" style="left:135px;top:2323px"><svg width="30" height="30"><rect x="2" y="2" width="26" height="26" rx="5" fill="#fff"/></svg></div>
<div class="card-name" style="left:221px;top:2333px">Lorem ipsum</div>
<div class="card-role" style="left:221px;top:2362px">Owner</div>

<div class="card-photo" style="left:446px;top:2100px;background:linear-gradient(160deg,#5a6068,#6e6a62 50%,#3e5a5a)" role="img" aria-label="Portrait photo of a smiling staff member"></div>
<div class="card-label" style="left:486px;top:2314px"></div>
<div class="card-icon" style="left:469px;top:2323px"><svg width="30" height="30"><rect x="2" y="2" width="26" height="26" rx="5" fill="#fff"/></svg></div>
<div class="card-name" style="left:555px;top:2333px">Duis aute irure</div>
<div class="card-role" style="left:555px;top:2362px">planner</div>

<div class="card-photo" style="left:779px;top:2100px;background:linear-gradient(160deg,#6a5a44,#c8b070 50%,#d8c46a)" role="img" aria-label="Portrait photo of a staff member in a library"></div>
<div class="card-label" style="left:819px;top:2314px"></div>
<div class="card-icon" style="left:802px;top:2323px"><svg width="30" height="30"><rect x="2" y="2" width="26" height="26" rx="5" fill="#fff"/></svg></div>
<div class="card-name" style="left:888px;top:2333px">Nemo enim</div>
<div class="card-role" style="left:888px;top:2362px">Manager</div>

<!-- Newsletter -->
<div class="abs newsletter"></div>
<div class="abs newsletter-photo" role="img" aria-label="Photo of a carer with a smiling elderly woman in a wheelchair"></div>
<h2 class="abs news-title">Subscribe To Our Newsletter</h2>
<div class="abs email">Email...</div>
<a class="btn" href="#" style="left:906px;top:2634px;width:154px;height:38px">Subscribe</a>

<!-- Footer -->
<footer class="abs footer"></footer>
<div class="abs footer-brand">Tidewell Clinic</div>
<div class="footer-nav">
  <a href="#" style="left:360px">Home</a>
  <a href="#" style="left:482px">About Us</a>
  <a href="#" style="left:601px">Staffs</a>
  <a href="#" style="left:698px">Blog</a>
  <a href="#" style="left:821px">Contact Us</a>
</div>
<span class="social" style="left:568px"></span>
<span class="social" style="left:606px"></span>
<div class="abs copyright">© 2024 Tidewell Clinic .All Rights Reserved</div>

</body>
</html>
```